International Travel Technology R&D business needs a wordpress website

We are a start up team of initially 2 individuals but plan to grow our team quickly, we have deep experience in travel technology. Our goal is to provide next generation technology research and development on behalf of our clients who are leading players in the travel technology industry. Attached our logos.

Target Market(s)

Travel Technology companies

Industry/Entity Type

Travel Industry

Coding

Coded - Design and coding required

Font styles to use
Sans Serif

Requirements
Must have
• Make use of our logo and colour scheme in the attached. Has to have a sense of adventure/ stepping into the unknown but equally must convey a sense of professionalism , we are a safe pair of hands. Sample themes are in the attachment .
Nice to have
• We have identified a theme on skinharbor which we feel would be inspirational. We hahe attached them to help in the design as inspiration.
Should not have
• images of airplanes , hotels etc, we want to project a future image.

```html
<!DOCTYPE html>
<html lang="en">
<head>
<meta charset="utf-8">
<title>Frontier Trip Labs</title>
<link href="https://fonts.googleapis.com/css2?family=Raleway:wght@300;400;500;600&family=Open+Sans:wght@400;600;700&display=swap" rel="stylesheet">
<style>
:root{
  --navy:#0d1b6e;
  --navy-band:#0c1a6b;
  --green:#67a53a;
  --label-green:#7aa84a;
  --ink:#222;
  --body:#444;
  --muted:#777;
  --white:#fff;
  --footer:#0d0d0d;
  --card:#ececec;
}
*{box-sizing:border-box;margin:0;padding:0}
html,body{width:1200px;height:2731px;overflow:hidden;background:#fff}
body{position:relative;font-family:"Open Sans",Arial,sans-serif;color:var(--ink)}
.abs{position:absolute}
.heading{font-family:"Raleway",Arial,sans-serif;font-weight:400;text-transform:uppercase}
.label{font-family:"Raleway",Arial,sans-serif;font-size:9px;letter-spacing:2px;color:var(--label-green);text-transform:uppercase;text-align:center;width:100%}
.btn{position:absolute;background:var(--navy);color:#fff;font-family:"Raleway",Arial,sans-serif;font-size:13px;font-weight:500;display:flex;align-items:center;justify-content:center;text-transform:uppercase}

/* hero */
.hero{left:0;top:0;width:1200px;height:519px;background:linear-gradient(180deg,#6d7fa8 0%,#c9a988 22%,#f1c98f 34%,#d7c3b4 48%,#9fb0c6 60%,#e8ecf2 72%,#f6f7f9 85%,#d8dde4 100%)}
.brand{left:131px;top:40px;display:flex;align-items:center;gap:10px;font-family:"Raleway",Arial,sans-serif;font-weight:600;font-size:20px;color:var(--navy);letter-spacing:1px}
.brand i{width:14px;height:14px;border-radius:50%;background:var(--navy);display:block}
.menu{left:1048px;top:12px}
.hero-title{left:0;top:226px;width:1200px;text-align:center;font-size:44px;color:var(--navy);letter-spacing:1px}
.hero-text{left:300px;top:287px;width:600px;text-align:center;font-size:13px;line-height:20px;color:#333}
.dots{left:1044px;top:390px;display:flex;flex-direction:column;gap:11px}
.dots span{width:9px;height:9px;border-radius:50%;background:#fff;display:block}

/* features */
.feature{top:590px;width:300px}
.feature .num{position:absolute;left:0;top:0;font-family:"Raleway",Arial,sans-serif;font-size:42px;font-weight:300;color:#111}
.feature .kicker{position:absolute;left:65px;top:2px;font-size:8px;color:#111;text-transform:uppercase}
.feature h3{position:absolute;left:65px;top:12px;font-size:28px;color:#111;font-weight:400}
.feature p{position:absolute;left:65px;top:56px;width:195px;font-size:10.5px;line-height:19px;color:var(--body);text-align:justify}

/* services */
.services-green{left:0;top:747px;width:537px;height:466px;background:var(--green)}
.services-photo{left:537px;top:747px;width:663px;height:466px;background:linear-gradient(120deg,#f4f2ef 0%,#ebe7e2 40%,#d9cfc4 70%,#c7b9aa 100%)}
.services-label{left:146px;top:842px;font-size:9px;letter-spacing:2px;color:#e8f3dc;font-family:"Raleway",Arial,sans-serif}
.services-title{left:146px;top:862px;font-size:42px;color:#fff;font-weight:300}
.services-rule{left:146px;top:920px;width:296px;height:2px;background:#fff}
.services-text{left:146px;top:936px;width:296px;font-size:10.5px;line-height:19px;color:#fff;font-weight:700;text-align:justify}
.services-panel{left:472px;top:840px;width:570px;height:311px;background:rgba(255,255,255,.85)}
.service{width:250px}
.service h4{position:absolute;left:40px;top:0;font-size:27px;color:#444;font-weight:300;font-family:"Raleway",Arial,sans-serif}
.service svg{position:absolute;left:0;top:8px}
.service p{position:absolute;left:40px;top:40px;width:195px;font-size:10.5px;line-height:19px;color:#333;text-align:justify}

/* clients */
.clients-title{left:0;top:1278px;width:1200px;text-align:center;font-size:42px;color:var(--navy);font-weight:300}
.client{width:130px;text-align:center;font-family:"Raleway",Arial,sans-serif;font-size:17px;color:#555;font-weight:500}

/* stats */
.stats{left:0;top:1639px;width:1200px;height:131px;background:var(--navy-band)}
.stat{top:1663px;color:#fff;font-family:"Raleway",Arial,sans-serif}
.stat .val{position:absolute;left:58px;top:0;font-size:28px;font-weight:400}
.stat .cap{position:absolute;left:58px;top:48px;font-size:19px;font-weight:400;white-space:nowrap}
.stat svg{position:absolute;left:0;top:2px}

/* testimonials */
.test-title{left:0;top:1818px;width:1200px;text-align:center;font-size:42px;color:#111;font-weight:400}
.card{top:1919px;width:247px;height:106px;background:var(--card)}
.card .avatar{position:absolute;left:14px;top:20px;width:60px;height:60px;border-radius:50%;background:linear-gradient(160deg,#c58b6a,#f0d2bd)}
.card p{position:absolute;left:90px;top:14px;width:148px;font-size:10px;line-height:13px;color:#666}
.card::after{content:"";position:absolute;right:20px;bottom:-12px;border-left:14px solid transparent;border-top:12px solid var(--card)}
.author{top:2036px;width:247px;text-align:right;padding-right:48px}
.author b{display:block;font-size:12px;color:var(--navy)}
.author span{display:block;font-size:9px;color:#555;margin-top:3px}

/* contact */
.contact{left:0;top:2134px;width:1200px;height:485px;background:linear-gradient(180deg,#7d9ab6 0%,#5c7f9f 35%,#3f6285 65%,#2f4f70 100%)}
.contact-title{left:0;top:2156px;width:1200px;text-align:center;font-size:44px;color:#fff;font-weight:300}
.contact-sub{left:0;top:2222px;width:1200px;text-align:center;font-size:12px;color:#fff;font-family:"Raleway",Arial,sans-serif}
.field{background:rgba(255,255,255,.55);font-size:11px;color:#333;padding:7px 14px}
.social{top:2504px;width:55px;height:55px;border:2px solid #fff;border-radius:50%;color:#fff;display:flex;align-items:center;justify-content:center;font-size:11px;font-weight:700}

/* footer */
.footer{left:0;top:2619px;width:1200px;height:112px;background:var(--footer)}
.news-label{left:164px;top:2658px;color:#fff;font-size:13px;font-weight:700}
.news-input{left:259px;top:2653px;width:172px;height:28px;background:#fff;font-size:11px;color:#333;padding:6px 10px}
.nav{left:590px;top:2651px;display:flex;gap:28px;color:#fff;font-size:10px;text-transform:uppercase}
.copy{left:779px;top:2684px;color:#ddd;font-size:10px}
</style>
</head>
<body>

<!-- hero -->
<div class="abs hero" role="img" aria-label="Photograph of skis standing in snow on a sunlit mountain summit"></div>
<div class="abs brand"><i></i>FRONTIER TRIP LABS</div>
<svg class="abs menu" width="24" height="24" viewBox="0 0 24 24"><rect x="3" y="6" width="18" height="2" fill="#fff"/><rect x="3" y="11" width="18" height="2" fill="#fff"/><rect x="3" y="16" width="18" height="2" fill="#fff"/></svg>
<h1 class="abs heading hero-title">Frontier Trip Labs</h1>
<p class="abs hero-text">Our goal is to provide next generation technology research and development on behalf of our clients who are leading players in the travel technology industry</p>
<div class="btn" style="left:546px;top:357px;width:106px;height:29px">Read more</div>
<div class="abs dots"><span></span><span></span><span></span><span></span><span></span></div>

<!-- features -->
<div class="abs feature" style="left:146px"><div class="num">01</div><div class="kicker">We are Frontier Trip Labs</div><h3 class="heading">Lorium Ipsum</h3><p>Duis aute irure dolor in reprehenderit in voluptate velit esse cillum dolore eu fugiat nulla pariatur.</p></div>
<div class="abs feature" style="left:470px"><div class="num">02</div><div class="kicker">We are Frontier Trip Labs</div><h3 class="heading">Lorium Ipsum</h3><p>Duis aute irure dolor in reprehenderit in voluptate velit esse cillum dolore eu fugiat nulla pariatur.</p></div>
<div class="abs feature" style="left:790px"><div class="num">03</div><div class="kicker">We are Frontier Trip Labs</div><h3 class="heading">Lorium Ipsum</h3><p>Duis aute irure dolor in reprehenderit in voluptate velit esse cillum dolore eu fugiat nulla pariatur.</p></div>

<!-- services -->
<div class="abs services-green"></div>
<div class="abs services-photo" role="img" aria-label="Photograph of professionals working at a bright office desk"></div>
<div class="abs services-label">LOREM IPSUM DOLOR AMET</div>
<h2 class="abs heading services-title">Our Services</h2>
<div class="abs services-rule"></div>
<p class="abs services-text">Lorem ipsum dolor sit amet, consectetur adipiscing elit, sed do eiusmod tempor incididunt ut labore et dolore magna aliqua. Ut enim ad minim veniam, quis nostrud exercitation ullamco laboris nisi ut aliquip ex ea commodo consequat. Duis aute irure dolor in reprehenderit in voluptate velit esse cillum dolore eu fugiat nulla pariatur.</p>
<div class="btn" style="left:146px;top:1087px;width:109px;height:29px">Read more</div>
<div class="abs services-panel"></div>
<div class="abs service" style="left:498px;top:878px">
  <svg width="24" height="24" viewBox="0 0 24 24"><path d="M20 3c-6 0-10 4-12 8l-3 1 2 2 2 2 2 2 1-3c4-2 8-6 8-12zM6 15l-3 6 6-3z" fill="#555"/></svg>
  <h4>LORIUM IPSUM</h4><p>Duis aute irure dolor in reprehenderit in voluptate velit esse cillum dolore eu fugiat nulla pariatur.</p></div>
<div class="abs service" style="left:773px;top:878px">
  <svg width="24" height="24" viewBox="0 0 24 24"><rect x="11" y="2" width="2" height="21" fill="#555"/><path d="M4 5h15l2 2-2 2H4zM20 11H5l-2 2 2 2h15z" fill="#555"/></svg>
  <h4>LORIUM IPSUM</h4><p>Duis aute irure dolor in reprehenderit in voluptate velit esse cillum dolore eu fugiat nulla pariatur.</p></div>
<div class="abs service" style="left:498px;top:1006px">
  <svg width="24" height="24" viewBox="0 0 24 24"><rect x="2" y="4" width="20" height="16" fill="none" stroke="#555" stroke-width="2"/><path d="M5 9h14M5 13h14M5 17h14" stroke="#555" stroke-width="2"/></svg>
  <h4>LORIUM IPSUM</h4><p>Duis aute irure dolor in reprehenderit in voluptate velit esse cillum dolore eu fugiat nulla pariatur.</p></div>
<div class="abs service" style="left:773px;top:1006px">
  <svg width="24" height="24" viewBox="0 0 24 24"><circle cx="12" cy="12" r="9" fill="none" stroke="#555" stroke-width="3"/><circle cx="12" cy="12" r="4" fill="none" stroke="#555" stroke-width="2"/></svg>
  <h4>LORIUM IPSUM</h4><p>Duis aute irure dolor in reprehenderit in voluptate velit esse cillum dolore eu fugiat nulla pariatur.</p></div>

<!-- clients -->
<div class="abs label" style="top:1261px;left:0">LOREM IPSUM DOLOR AMET</div>
<h2 class="abs heading clients-title">Our Clients</h2>
<div class="abs client" style="left:199px;top:1405px">Orvelle</div>
<div class="abs client" style="left:339px;top:1405px">Kestrel</div>
<div class="abs client" style="left:490px;top:1405px">Harbor Fair</div>
<div class="abs client" style="left:618px;top:1405px">Lumara</div>
<div class="abs client" style="left:744px;top:1405px">Brightfield</div>
<div class="abs client" style="left:873px;top:1405px">Corvin's</div>
<div class="abs client" style="left:199px;top:1521px">Crafthaus</div>
<div class="abs client" style="left:339px;top:1521px">Velisse</div>
<div class="abs client" style="left:490px;top:1521px">Trustmere</div>
<div class="abs client" style="left:618px;top:1521px">Norik</div>
<div class="abs client" style="left:744px;top:1521px">Verdaline</div>
<div class="abs client" style="left:873px;top:1521px">Quillsoft</div>

<!-- stats -->
<div class="abs stats"></div>
<div class="abs stat" style="left:169px"><svg width="36" height="36" viewBox="0 0 36 36" fill="none" stroke="#fff" stroke-width="2"><circle cx="18" cy="11" r="7"/><path d="M4 33c1-9 7-13 14-13s13 4 14 13z"/></svg><div class="val">1000+</div><div class="cap">Happy users</div></div>
<div class="abs stat" style="left:401px"><svg width="36" height="36" viewBox="0 0 36 36" fill="none" stroke="#fff" stroke-width="2"><path d="M3 5h5l4 18h17l4-13H10"/><circle cx="14" cy="29" r="2.5"/><circle cx="27" cy="29" r="2.5"/></svg><div class="val">200</div><div class="cap">Sold products</div></div>
<div class="abs stat" style="left:625px"><svg width="36" height="36" viewBox="0 0 36 36" fill="none" stroke="#fff" stroke-width="2"><path d="M3 4h24v17H14l-6 6v-6H3z"/><path d="M27 11h6v16h-4v5l-5-5H13v-3"/></svg><div class="val">5632</div><div class="cap">Comments</div></div>
<div class="abs stat" style="left:856px"><svg width="36" height="36" viewBox="0 0 36 36" fill="none" stroke="#fff" stroke-width="2"><path d="M12 3h12l6 6v19H12z"/><path d="M24 3v6h6"/><path d="M12 9H6v24h18v-5"/></svg><div class="val">25000+</div><div class="cap">Lines of code</div></div>

<!-- testimonials -->
<div class="abs label" style="top:1801px;left:0">LOREM IPSUM DOLOR AMET</div>
<h2 class="abs heading test-title">Testimonials</h2>
<div class="abs card" style="left:209px"><div class="avatar" role="img" aria-label="Portrait photo of the reviewer"></div><p>Nor again is there anyone who loves or pursues or desires to obtain pain of itself, because it is pain, but because occasionally circumstances occur</p></div>
<div class="abs card" style="left:481px"><div class="avatar" role="img" aria-label="Portrait photo of the reviewer"></div><p>Nor again is there anyone who loves or pursues or desires to obtain pain of itself, because it is pain, but because occasionally circumstances occur</p></div>
<div class="abs card" style="left:756px"><div class="avatar" role="img" aria-label="Portrait photo of the reviewer"></div><p>Nor again is there anyone who loves or pursues or desires to obtain pain of itself, because it is pain, but because occasionally circumstances occur</p></div>
<div class="abs author" style="left:209px"><b>June Harper</b><span>CEO - Lorium ipsum</span></div>
<div class="abs author" style="left:481px"><b>June Harper</b><span>CEO - Lorium ipsum</span></div>
<div class="abs author" style="left:756px"><b>June Harper</b><span>CEO - Lorium ipsum</span></div>

<!-- contact -->
<div class="abs contact" role="img" aria-label="Aerial photograph of a modern city skyline with glass towers"></div>
<h2 class="abs heading contact-title">Contact Us</h2>
<div class="abs contact-sub">CONTACT US FOR DETAILS OF OUR WORKS</div>
<div class="abs field" style="left:346px;top:2262px;width:255px;height:33px">Name</div>
<div class="abs field" style="left:612px;top:2262px;width:257px;height:33px">Email</div>
<div class="abs field" style="left:346px;top:2305px;width:523px;height:33px">Subject</div>
<div class="abs field" style="left:346px;top:2349px;width:523px;height:73px">Message</div>
<div class="btn" style="left:550px;top:2449px;width:113px;height:33px;font-size:10px;font-weight:700">Send message</div>
<div class="abs social" style="left:505px">Fb</div>
<div class="abs social" style="left:578px">Ch</div>
<div class="abs social" style="left:650px">Ww</div>

<!-- footer -->
<div class="abs footer"></div>
<div class="abs news-label">NEWSLETTER</div>
<div class="abs news-input">Enter Email id
  <svg style="position:absolute;right:8px;top:8px" width="12" height="12" viewBox="0 0 12 12"><path d="M1 6l10-5-4 10-1-4z" fill="#333"/></svg></div>
<div class="abs nav"><span>Home</span><span>Company</span><span>Services</span><span>Blog</span><span>Testimonials</span><span>Contact</span></div>
<div class="abs copy">© Copyright 2016, www.companyname.com</div>

</body>
</html>
```